Kelvor Engineers: Why you should hire us keepsake

New design. Open to plastic cards. We are an engineering firm that designs cell phone towers and commercial buildings. Please check out our website www.kelvorstruct.com for more details. We want people to remember our card and for it to be useful if possible. We want the same look and feel on these cards to be translated to other marketing material we may need such as brochures.

Target Market(s)

Architects, Developers and Telecommunication Carriers

Industry/Entity Type

Engineering

Contact Information for Business Card

Card with our company colors, logo, and innovative design with elements related to our industry.

Font styles to use
Sans Serif

Colors
9bcb3c
abd036
0255a3

Requirements
Must have
• Sleek and hip design
Nice to have
• Bright lime green and navy coloring that pops with an innovative design.
Should not have
• A basic and boring design

```html
<!DOCTYPE html>
<html lang="en">
<head>
<meta charset="utf-8">
<title>Kelvor Engineers – Business Card</title>
<link href="https://fonts.googleapis.com/css2?family=Oswald:wght@500&family=Roboto:wght@400;500;900&display=swap" rel="stylesheet">
<style>
  :root {
    --lime: #cad42a;
    --lime-bright: #d3da2e;
    --navy: #1d3767;
    --white: #ffffff;
    --stage: #2b2b2b;
  }
  * { margin: 0; padding: 0; box-sizing: border-box; }
  html, body { width: 1200px; height: 930px; overflow: hidden; background: var(--stage); }
  body { position: relative; font-family: "Roboto", sans-serif; }

  .card {
    position: absolute;
    width: 640px;
    height: 366px;
    border-radius: 22px;
    overflow: hidden;
    box-shadow: 0 10px 30px rgba(0,0,0,.45);
  }

  /* Front */
  .card-front { left: 90px; top: 70px; background: var(--lime); }
  .front-name {
    position: absolute; left: 0; right: 0; top: 118px;
    text-align: center;
    font-weight: 900; font-size: 62px; letter-spacing: -1px;
    color: var(--white);
  }
  .front-cities {
    position: absolute; left: 40px; bottom: 34px;
    font-weight: 500; font-size: 17px; letter-spacing: 1.5px;
    color: var(--white); text-transform: uppercase;
  }
  .front-cities .sep { margin: 0 8px; opacity: .85; }

  /* Back */
  .card-back { left: 470px; top: 490px; background: var(--white); }
  .card-back svg.waves { position: absolute; inset: 0; }
  .brand { position: absolute; left: 34px; top: 124px; }
  .brand-name {
    font-weight: 900; font-size: 33px; color: var(--lime); letter-spacing: -.5px;
    white-space: nowrap;
  }
  .brand-tagline {
    margin-top: 2px;
    font-family: "Oswald", sans-serif; font-weight: 500;
    font-size: 17px; color: var(--navy); letter-spacing: .5px;
    text-transform: uppercase; white-space: nowrap;
  }
  .contact {
    position: absolute; right: 24px; top: 96px;
    text-align: right; color: var(--white);
  }
  .contact-name { font-size: 20px; font-weight: 500; white-space: nowrap; }
  .contact-title { font-size: 14px; color: var(--lime-bright); margin-top: 2px; margin-bottom: 12px; }
  .contact-line {
    display: flex; justify-content: flex-end; align-items: center; gap: 9px;
    font-size: 13.5px; line-height: 20px; white-space: nowrap;
  }
  .contact-line svg { width: 11px; height: 11px; flex: none; }
</style>
</head>
<body>

  <section class="card card-front" aria-label="Card front">
    <div class="front-name">Kelvor Engineers</div>
    <div class="front-cities">Atlanta<span class="sep">|</span>Charlotte<span class="sep">|</span>Houston<span class="sep">|</span>San Antonio</div>
  </section>

  <section class="card card-back" aria-label="Card back">
    <svg class="waves" viewBox="0 0 640 366" width="640" height="366" aria-hidden="true">
      <defs>
        <path id="wave-shape" d="M700,14 L640,14 C470,14 400,50 360,130 C325,200 290,258 0,270 L-60,271 L-60,420 L700,420 Z"/>
      </defs>
      <use href="#wave-shape" fill="var(--navy)"/>
      <use href="#wave-shape" fill="var(--white)" transform="translate(8,5)"/>
      <use href="#wave-shape" fill="var(--lime)" transform="translate(13,9)"/>
      <use href="#wave-shape" fill="var(--navy)" transform="translate(24,17)"/>
    </svg>

    <div class="brand">
      <div class="brand-name">Kelvor Engineers</div>
      <div class="brand-tagline">Multi-Discipline Engineering</div>
    </div>

    <div class="contact">
      <div class="contact-name">Dana Whitlow Marsh</div>
      <div class="contact-title">Director</div>
      <div class="contact-line">555.201.4417
        <svg viewBox="0 0 12 12"><path d="M2 1 L4 1 L5 4 L3.5 5 C4.3 6.8 5.2 7.7 7 8.5 L8 7 L11 8 L11 10 C11 10.6 10.6 11 10 11 C5 11 1 7 1 2 C1 1.4 1.4 1 2 1Z" fill="var(--lime-bright)"/></svg>
      </div>
      <div class="contact-line">555.318.6624
        <svg viewBox="0 0 12 12"><rect x="3" y="0.5" width="6" height="11" rx="1.2" fill="none" stroke="var(--lime-bright)" stroke-width="1.2"/></svg>
      </div>
      <div class="contact-line">dmarsh@kelvorstruct.com
        <svg viewBox="0 0 12 12"><rect x="0.6" y="2" width="10.8" height="8" rx="1" fill="none" stroke="var(--lime-bright)" stroke-width="1.2"/><path d="M1 2.5 L6 6.5 L11 2.5" fill="none" stroke="var(--lime-bright)" stroke-width="1.2"/></svg>
      </div>
      <div class="contact-line">www.kelvorstruct.com
        <svg viewBox="0 0 12 12"><circle cx="6" cy="6" r="5.2" fill="none" stroke="var(--lime-bright)" stroke-width="1.2"/><path d="M1 6 H11 M6 1 C3.5 4 3.5 8 6 11 M6 1 C8.5 4 8.5 8 6 11" fill="none" stroke="var(--lime-bright)" stroke-width="1"/></svg>
      </div>
    </div>
  </section>

</body>
</html>
```